Figure for presentation on a hybrid research project

We need a figure that shows a series of 6 technical projects feeding into 3 multidisciplinary hybrid projects.
The concept is a ring of 6 technical projects, which could look like a 6 colour swirl (see
https://en.plorvanex.org/wiki/Vector_graphics for an example of a 4 colour swirl.)
The 3 hybrid projects sit in the centre because they rely on input from many of the surrounding technical projects.
I've drawn a rough version in Powerpoint - see attached file uploaded. Note, in my example I couldn't draw the swirling outer ring and the colour selection is poor. The acronym for the overall Centre using the figure is VexORDA, so we will have a mint leaf and turquoise green in the logo, plus also nerves, since we will be researching neural interconnections.
We ABSOLUTELY NEED the final form of the figure to include vector graphics formats (including a form that can be edited in Photoshop) because we may need to change the title of the technical projects or of the hybrid projects at short notice ourselves.

Target Market(s)

Academic: eminent scientists and engineers

Industry/Entity Type

Technical

Font styles to use
Sans Serif

Colors
04a990

Requirements
Must have
• The projects around the ring with all project titles legible; the final figure will be reduced to no more than 8cm x 8cm in the proposal (probably less).
• Only one colour selected, because we have included that colour in the logo that we are having designed. Otherwise, a colour series around the ring that is pleasant, and another compatible colour series for the inter 3 projects.
• We ABSOLUTELY NEED the final form of the figure to include vector graphics formats (including a form that can be edited in Photoshop) because we may need to change the title of the technical projects or of the hybrid projects at short notice ourselves.
Nice to have
• See the figure we uploaded; that's the essence
• HOWEVER VIP: two of the titles around the outer ring have changed slightly.
• Computational Modelling is now Neuronal Modelling and
• Signal Processing is now Non-Invasive Interfaces (note that I've now changed the titles on the uploaded figure)

```html
<!DOCTYPE html>
<html lang="en">
<head>
<meta charset="utf-8">
<title>VexORDA Research Programme Structure</title>
<link rel="stylesheet" href="https://fonts.googleapis.com/css2?family=Outfit:wght@600;700;800&display=swap">
<style>
  :root {
    --page-bg: #ffffff;
    --petal-light: #04a990;
    --petal-light-deep: #02866f;
    --petal-dark: #087a62;
    --petal-dark-deep: #045a48;
    --hub-action: #1a7af6;
    --hub-action-deep: #0b5fe2;
    --hub-wiring: #0b44e2;
    --hub-wiring-deep: #0626b4;
    --hub-perception: #0a2ea8;
    --hub-perception-deep: #061f86;
    --divider: #ffffff;
    --label: #ffffff;
  }
  html, body {
    margin: 0;
    padding: 0;
    width: 1200px;
    height: 999px;
    overflow: hidden;
    background: var(--page-bg);
  }
  .programme-figure {
    position: relative;
    width: 1200px;
    height: 999px;
  }
  .programme-figure svg {
    position: absolute;
    inset: 0;
    display: block;
  }
  .petal-edge {
    fill: none;
    stroke: var(--divider);
    stroke-width: 6;
  }
  .hub-lobe {
    stroke: var(--divider);
    stroke-width: 5;
    stroke-linejoin: round;
  }
  .hub-rim {
    fill: none;
    stroke: var(--divider);
    stroke-width: 6;
  }
  .project-title {
    font-family: "Outfit", sans-serif;
    font-weight: 600;
    font-size: 24px;
    letter-spacing: 0.4px;
    fill: var(--label);
  }
  .hybrid-title {
    font-family: "Outfit", sans-serif;
    font-weight: 800;
    font-size: 27px;
    fill: var(--label);
    text-anchor: middle;
  }
</style>
</head>
<body>
<main class="programme-figure">
  <svg viewBox="0 0 1200 999" width="1200" height="999" role="img" aria-label="Six technical projects in a swirling ring around three hybrid projects">
    <defs>
      <linearGradient id="grad-living" x1="0" y1="0" x2="1" y2="1">
        <stop offset="0" stop-color="var(--petal-dark)"/><stop offset="1" stop-color="var(--petal-dark-deep)"/>
      </linearGradient>
      <linearGradient id="grad-gene" x1="0" y1="0" x2="0" y2="1">
        <stop offset="0" stop-color="var(--petal-light)"/><stop offset="1" stop-color="var(--petal-light-deep)"/>
      </linearGradient>
      <linearGradient id="grad-electro" x1="1" y1="0" x2="0" y2="1">
        <stop offset="0" stop-color="var(--petal-dark)"/><stop offset="1" stop-color="var(--petal-dark-deep)"/>
      </linearGradient>
      <linearGradient id="grad-optrode" x1="1" y1="1" x2="0" y2="0">
        <stop offset="0" stop-color="var(--petal-light)"/><stop offset="1" stop-color="var(--petal-light-deep)"/>
      </linearGradient>
      <linearGradient id="grad-neuronal" x1="0" y1="1" x2="1" y2="0">
        <stop offset="0" stop-color="var(--petal-dark)"/><stop offset="1" stop-color="var(--petal-dark-deep)"/>
      </linearGradient>
      <linearGradient id="grad-noninvasive" x1="0" y1="1" x2="1" y2="0">
        <stop offset="0" stop-color="var(--petal-light)"/><stop offset="1" stop-color="var(--petal-light-deep)"/>
      </linearGradient>

      <radialGradient id="grad-action" cx="0.35" cy="0.35" r="0.8">
        <stop offset="0" stop-color="var(--hub-action)"/><stop offset="1" stop-color="var(--hub-action-deep)"/>
      </radialGradient>
      <radialGradient id="grad-wiring" cx="0.5" cy="0.4" r="0.8">
        <stop offset="0" stop-color="var(--hub-wiring)"/><stop offset="1" stop-color="var(--hub-wiring-deep)"/>
      </radialGradient>
      <radialGradient id="grad-perception" cx="0.5" cy="0.3" r="0.8">
        <stop offset="0" stop-color="var(--hub-perception)"/><stop offset="1" stop-color="var(--hub-perception-deep)"/>
      </radialGradient>

      <filter id="edge-depth" x="-20%" y="-20%" width="140%" height="140%">
        <feDropShadow dx="0" dy="0" stdDeviation="8" flood-color="#003328" flood-opacity="0.45"/>
      </filter>

      <mask id="under-noninvasive" maskUnits="userSpaceOnUse" x="0" y="0" width="1200" height="999">
        <rect width="1200" height="999" fill="#fff"/><circle cx="473.4" cy="520" r="265" fill="#000"/>
      </mask>
      <mask id="under-living" maskUnits="userSpaceOnUse" x="0" y="0" width="1200" height="999">
        <rect width="1200" height="999" fill="#fff"/><circle cx="473.4" cy="420" r="265" fill="#000"/>
      </mask>
      <mask id="under-gene" maskUnits="userSpaceOnUse" x="0" y="0" width="1200" height="999">
        <rect width="1200" height="999" fill="#fff"/><circle cx="560" cy="370" r="265" fill="#000"/>
      </mask>
      <mask id="under-electro" maskUnits="userSpaceOnUse" x="0" y="0" width="1200" height="999">
        <rect width="1200" height="999" fill="#fff"/><circle cx="646.6" cy="420" r="265" fill="#000"/>
      </mask>
      <mask id="under-optrode" maskUnits="userSpaceOnUse" x="0" y="0" width="1200" height="999">
        <rect width="1200" height="999" fill="#fff"/><circle cx="646.6" cy="520" r="265" fill="#000"/>
      </mask>
      <mask id="under-neuronal" maskUnits="userSpaceOnUse" x="0" y="0" width="1200" height="999">
        <rect width="1200" height="999" fill="#fff"/><circle cx="560" cy="570" r="265" fill="#000"/>
      </mask>

      <path id="arc-living" d="M267.5 427.2 A206 206 0 0 1 664.4 342.8"/>
      <path id="arc-gene" d="M450.8 195.3 A206 206 0 0 1 722.3 496.8"/>
      <path id="arc-noninvasive" d="M376.7 701.9 A206 206 0 0 1 502.1 316"/>
      <path id="arc-electro" d="M615.4 641.8 A224 224 0 0 0 751.8 222.2"/>
      <path id="arc-optrode" d="M438.9 603.9 A224 224 0 0 0 870.5 512.2"/>
      <path id="arc-neuronal" d="M383.5 432.1 A224 224 0 0 0 678.7 760"/>
    </defs>

    <g class="technical-ring">
      <g class="petal-fills">
        <circle class="petal petal--living" cx="473.4" cy="420" r="265" fill="url(#grad-living)" mask="url(#under-noninvasive)"/>
        <circle class="petal petal--gene" cx="560" cy="370" r="265" fill="url(#grad-gene)" mask="url(#under-living)"/>
        <circle class="petal petal--electro" cx="646.6" cy="420" r="265" fill="url(#grad-electro)" mask="url(#under-gene)"/>
        <circle class="petal petal--optrode" cx="646.6" cy="520" r="265" fill="url(#grad-optrode)" mask="url(#under-electro)"/>
        <circle class="petal petal--neuronal" cx="560" cy="570" r="265" fill="url(#grad-neuronal)" mask="url(#under-optrode)"/>
        <circle class="petal petal--noninvasive" cx="473.4" cy="520" r="265" fill="url(#grad-noninvasive)" mask="url(#under-neuronal)"/>
      </g>
      <g class="petal-edges" filter="url(#edge-depth)">
        <circle class="petal-edge" cx="473.4" cy="420" r="265" mask="url(#under-noninvasive)"/>
        <circle class="petal-edge" cx="560" cy="370" r="265" mask="url(#under-living)"/>
        <circle class="petal-edge" cx="646.6" cy="420" r="265" mask="url(#under-gene)"/>
        <circle class="petal-edge" cx="646.6" cy="520" r="265" mask="url(#under-electro)"/>
        <circle class="petal-edge" cx="560" cy="570" r="265" mask="url(#under-optrode)"/>
        <circle class="petal-edge" cx="473.4" cy="520" r="265" mask="url(#under-neuronal)"/>
      </g>
    </g>

    <g class="technical-titles">
      <text class="project-title"><textPath href="#arc-living" startOffset="50%" text-anchor="middle">Living Electrodes</textPath></text>
      <text class="project-title"><textPath href="#arc-gene" startOffset="50%" text-anchor="middle">Gene Regulated Interfaces</textPath></text>
      <text class="project-title"><textPath href="#arc-electro" startOffset="50%" text-anchor="middle">Electro-modulated Interfaces</textPath></text>
      <text class="project-title"><textPath href="#arc-optrode" startOffset="50%" text-anchor="middle">Optrode Interfaces</textPath></text>
      <text class="project-title"><textPath href="#arc-neuronal" startOffset="50%" text-anchor="middle">Neuronal Modeling</textPath></text>
      <text class="project-title"><textPath href="#arc-noninvasive" startOffset="50%" text-anchor="middle">Non-invasive Interfaces</textPath></text>
    </g>

    <g class="hybrid-hub" filter="url(#edge-depth)">
      <path class="hub-lobe hub-lobe--wiring" fill="url(#grad-wiring)"
            d="M560 470 A100 100 0 0 1 585 291.8 A180 180 0 0 1 701.8 580.8 A100 100 0 0 0 560 470 Z"/>
      <path class="hub-lobe hub-lobe--perception" fill="url(#grad-perception)"
            d="M560 470 A100 100 0 0 1 701.8 580.8 A180 180 0 0 1 393.1 537.4 A100 100 0 0 0 560 470 Z"/>
      <path class="hub-lobe hub-lobe--action" fill="url(#grad-action)"
            d="M560 470 A100 100 0 0 1 393.1 537.4 A180 180 0 0 1 585 291.8 A100 100 0 0 0 560 470 Z"/>
      <circle class="hub-rim" cx="560" cy="470" r="180"/>
    </g>

    <g class="hybrid-titles">
      <text class="hybrid-title" x="457" y="455">ACTION</text>
      <text class="hybrid-title" x="622" y="389">BRAIN</text>
      <text class="hybrid-title" x="624" y="426">WIRING</text>
      <text class="hybrid-title" x="562" y="597">PERCEPTION</text>
    </g>
  </svg>
</main>
</body>
</html>
```